Web Design Project for Communications Agency

The design I need (PSD file) is for an agency offering specialised PR and communications services for customers in the healthcare sector.

OBJECTIVES OF THE WEBSITE:
1. To promote the agency's communication services
2. To position Solène Brivard as an industry leader, an expert in healthcare PR and communications by highlighting blogposts and social media.

WHAT I NEED:
1st, I need the design for the Home Page ONLY.
Once approved, I will need the other pages designed as well. (Here is prototype that we've already developed for the Website that will guide you in the design:
http://qorvelle.net/solenebrivard/)

VISUAL INSPIRATION
We want to give this Website a "Flat Design" look. Here are some websites for inspiration :
- http://tavrolinkworks.com/#!/process
- http://www.brindlemoss.co/
- http://quellaroft.com/

Also, reuse images found on the company's current Website :
http://www.solenebrivard.com/fr/index.html

HOMEPAGE MAIN ELEMENTS:
1. Main menu : 6 sections
Accueil | Agence | Services | Approche | Publications | Contact

2. Main Call To Action (big dark rectangle in prototype):
Can be slider or just an information bloc.

3. Publications récentes :
The 4 latest blog posts must be features on the homepage (will be linked with the "Publications" section)

4. Dynamic Footer :
Contains a Twitter feed and a Subscribe to our Newsletter feature (revecez nos publications)

OTHER PAGES (to design once Homepage is approved)
- Agence (about us)
- Services (our team)
- Approche (our approach)
- Publications (blog articles)
- Contact (Contact us)

Industry/Entity Type

Communications

Requirements
Must have
• Please refer to prototype :
http://qorvelle.net/solenebrivard/
Must have ALL features present in prototype.

Also, must reuse this picture in the design : http://solenebrivard.com/static/images/home-big-box.jpg

Finally, you will find attached the company logo.

```html
<!DOCTYPE html>
<html lang="fr">
<head>
<meta charset="utf-8">
<title>Solène Brivard – Gestion d'enjeux, affaires publiques</title>
<link href="https://fonts.googleapis.com/css2?family=Open+Sans:ital,wght@0,400;0,600;1,400&display=swap" rel="stylesheet">
<style>
:root{
  --ink:#2b2b2b;
  --muted:#6a6a6a;
  --brand-red:#d9262b;
  --button-red:#c0151b;
  --orange:#c9641c;
  --orange-light:#e07a2c;
  --band-dark:#231a17;
  --light-gray:#f5f5f5;
  --box-gray:#efefef;
  --slate:#56595c;
  --slate-text:#b3b6b8;
  --white:#ffffff;
  --rule:#7a7d80;
  --icon-gray:#b9b9b9;
}
*{margin:0;padding:0;box-sizing:border-box}
html,body{width:1200px;height:2203px;overflow:hidden}
body{position:relative;font-family:'Open Sans',sans-serif;color:var(--ink);background:var(--white)}
.abs{position:absolute}

/* Hero */
.hero{left:0;top:0;width:1200px;height:567px;
  background:radial-gradient(ellipse at 50% 40%,#8a5a44 0%,#5e3a2c 45%,#3a241c 100%)}
.hero-title{left:0;top:282px;width:1200px;text-align:center;color:var(--white);
  font-size:39px;font-weight:600;line-height:48px;text-shadow:0 2px 6px rgba(0,0,0,.45)}
.cta-band{left:0;top:567px;width:1200px;height:79px;background:var(--band-dark);border-bottom:3px solid var(--orange)}
.cta-button{left:429px;top:567px;width:364px;height:79px;display:flex;text-decoration:none}
.cta-label{width:282px;background:var(--orange);color:var(--white);font-size:33px;font-weight:600;
  line-height:79px;padding-left:22px}
.cta-arrow{width:82px;background:var(--orange-light);display:flex;align-items:center;justify-content:center}

/* Header */
.site-header{left:110px;top:0;width:980px;height:112px;background:rgba(255,255,255,.96);box-shadow:0 2px 6px rgba(0,0,0,.15)}
.brand{left:16px;top:14px;display:flex;align-items:center;gap:10px}
.brand-mark{width:12px;height:12px;background:var(--brand-red)}
.brand-name{color:var(--brand-red);font-size:34px;font-weight:600;line-height:36px;width:140px;letter-spacing:-.5px}
.brand-tagline{left:148px;top:54px;font-size:13px;font-weight:600;color:#444;line-height:16px;letter-spacing:.5px}
.social-top{left:694px;top:12px;display:flex;gap:8px}
.social-top span{width:23px;height:23px;border-radius:50%;background:var(--icon-gray);display:block}
.lang{left:871px;top:12px;width:94px;height:20px;border:1px solid #888;font-size:12px;line-height:18px;padding-left:4px;color:#333;background:var(--white)}
.lang i{position:absolute;right:1px;top:1px;width:16px;height:16px;background:#333}
.lang i::after{content:"";position:absolute;left:4px;top:6px;border:4px solid transparent;border-top-color:var(--white)}
.main-nav{right:18px;top:78px;display:flex;gap:32px;font-size:13px;text-transform:uppercase;color:#333}
.main-nav a{color:inherit;text-decoration:none;display:flex;align-items:center;gap:5px}

/* Publications */
.section-title{left:117px;top:705px;width:303px;height:57px;background:var(--box-gray);
  font-size:27px;font-weight:600;line-height:57px;padding-left:17px}
.post-band{left:0;top:1058px;width:1200px;height:291px;background:var(--light-gray)}
.post-text{width:616px}
.post-title{font-size:15px;line-height:19px;color:#222}
.post-date{font-size:14px;font-style:italic;line-height:19px;color:#222}
.post-excerpt{margin-top:16px;font-size:12px;line-height:18px;color:var(--muted)}
.read-more{height:36px;width:160px;background:var(--box-gray);display:flex;align-items:center;gap:10px;
  padding-left:14px;font-size:14px;color:var(--button-red);text-decoration:none}
.post-band .read-more{background:var(--white)}
.post-photo{border:3px solid #ddd;box-shadow:0 10px 10px -6px rgba(0,0,0,.35)}

/* Twitter */
.twitter-feed{left:0;top:1692px;width:1200px;height:284px}
.tweet{left:0;top:1826px;width:1200px;text-align:center;font-size:25px;line-height:34px;color:var(--slate-text)}
.tweet b{font-weight:400;color:var(--white)}
.follow{left:0;top:1908px;width:1200px;text-align:center;font-size:20px;color:var(--slate-text)}
.follow b{font-weight:600;color:var(--white)}

/* Footer */
.footer-head{font-size:14px;font-weight:600;color:#e0534f;text-transform:uppercase;letter-spacing:.5px}
.footer-links{list-style:none;margin-top:20px;font-size:13px;line-height:22px}
.footer-links a{color:#333;text-decoration:none}
.connect-icons{display:flex;gap:6px;margin-top:24px}
.connect-icons span{width:28px;height:28px;background:#ddd;display:block}
.copyright{margin-top:9px;font-size:12px;color:#555}
.field{width:273px;height:33px;background:var(--box-gray);border:1px solid #ddd;font-size:15px;color:#999;line-height:31px;padding-left:12px;margin-top:8px}
.subscribe{margin-top:11px;width:160px;height:35px;background:var(--button-red);color:var(--white);font-size:15px;font-weight:600;text-align:center;line-height:35px;box-shadow:0 2px 3px rgba(0,0,0,.3)}
</style>
</head>
<body>

<div class="abs hero" role="img" aria-label="Photo floue d'une salle de conférence avec un public assis face à un écran"></div>
<h1 class="abs hero-title">Cabinet-conseil en communications et affaires<br>publiques spécialisé dans le secteur de la santé.</h1>
<div class="abs cta-band"></div>
<a class="abs cta-button" href="#agence">
  <span class="cta-label">En savoir plus</span>
  <span class="cta-arrow"><svg width="48" height="48" viewBox="0 0 48 48"><circle cx="24" cy="24" r="20" fill="none" stroke="#fff" stroke-width="4"/><path d="M13 24h20M25 15l9 9-9 9" fill="none" stroke="#fff" stroke-width="4"/></svg></span>
</a>

<header class="abs site-header">
  <div class="abs brand"><span class="brand-name">Solène Brivard</span></div>
  <div class="abs brand-tagline">GESTION D'ENJEUX<br>AFFAIRES PUBLIQUES</div>
  <div class="abs social-top"><span></span><span></span><span></span><span></span>
    <svg width="23" height="23" viewBox="0 0 23 23"><circle cx="11.5" cy="11.5" r="11.5" fill="#b9b9b9"/><circle cx="10" cy="10" r="4.5" fill="none" stroke="#fff" stroke-width="2"/><path d="M13.5 13.5l4 4" stroke="#fff" stroke-width="2.5"/></svg>
  </div>
  <div class="abs lang">English<i></i></div>
  <nav class="abs main-nav">
    <a href="#"><svg width="14" height="12" viewBox="0 0 14 12"><path d="M7 0L0 6h2v6h4V8h2v4h4V6h2z" fill="#d9262b"/></svg>Accueil</a>
    <a href="#">Agence</a><a href="#">Services</a><a href="#">Approche</a><a href="#">Publications</a><a href="#">Contact</a>
  </nav>
</header>

<h2 class="abs section-title">Publication récentes</h2>

<article class="abs post-text" style="left:117px;top:801px">
  <h3 class="post-title" style="font-weight:400">Titre de la publication</h3>
  <p class="post-date">23 juillet 2013</p>
  <p class="post-excerpt">Lorem ipsum dolor sit amet, consectetur adipisicing elit, sed do eiusmod tempor incididunt ut labore et dolore magna aliqua. Ut enim ad minim veniam, quis nostrud exercitation ullamco laboris nisi ut aliquip ex ea commodo consequat. Duis aute irure dolor in reprehenderit in voluptate velit esse cillum dolore eu fugiat nulla pariatur.</p>
</article>
<a class="abs read-more" style="left:112px;top:972px" href="#">Article complet<svg width="18" height="18" viewBox="0 0 18 18"><circle cx="9" cy="9" r="7.5" fill="none" stroke="#c0151b" stroke-width="1.6"/><path d="M5 9h7M9 6l3 3-3 3" fill="none" stroke="#c0151b" stroke-width="1.6"/></svg></a>
<div class="abs post-photo" style="left:774px;top:779px;width:310px;height:217px;background:linear-gradient(135deg,#9fb4c8,#dfe6ec 55%,#8fa6bd)" role="img" aria-label="Photo d'une équipe médicale en blouses discutant dans un hall d'hôpital"></div>

<div class="abs post-band"></div>
<div class="abs post-photo" style="left:116px;top:1088px;width:325px;height:227px;background:linear-gradient(160deg,#cfd3d6,#6c6f73 60%,#3b3d40)" role="img" aria-label="Photo de quatre personnes posant devant un panneau d'événement"></div>
<article class="abs post-text" style="left:458px;top:1096px;width:620px">
  <h3 class="post-title" style="font-weight:400">Titre de la publication</h3>
  <p class="post-date">23 juillet 2013</p>
  <p class="post-excerpt" style="margin-top:24px">Lorem ipsum dolor sit amet, consectetur adipisicing elit, sed do eiusmod tempor incididunt ut labore et dolore magna aliqua. Ut enim ad minim veniam, quis nostrud exercitation ullamco laboris nisi ut aliquip ex ea commodo consequat. Duis aute irure dolor in reprehenderit in voluptate velit esse cillum dolore eu fugiat nulla pariatur.</p>
</article>
<a class="abs read-more" style="left:458px;top:1276px" href="#">Article complet<svg width="18" height="18" viewBox="0 0 18 18"><circle cx="9" cy="9" r="7.5" fill="none" stroke="#c0151b" stroke-width="1.6"/><path d="M5 9h7M9 6l3 3-3 3" fill="none" stroke="#c0151b" stroke-width="1.6"/></svg></a>

<article class="abs post-text" style="left:117px;top:1402px">
  <h3 class="post-title" style="font-weight:400">Titre de la publication</h3>
  <p class="post-date">23 juillet 2013</p>
  <p class="post-excerpt">Lorem ipsum dolor sit amet, consectetur adipisicing elit, sed do eiusmod tempor incididunt ut labore et dolore magna aliqua. Ut enim ad minim veniam, quis nostrud exercitation ullamco laboris nisi ut aliquip ex ea commodo consequat. Duis aute irure dolor in reprehenderit in voluptate velit esse cillum dolore eu fugiat nulla pariatur.</p>
</article>
<a class="abs read-more" style="left:112px;top:1579px" href="#">Article complet<svg width="18" height="18" viewBox="0 0 18 18"><circle cx="9" cy="9" r="7.5" fill="none" stroke="#c0151b" stroke-width="1.6"/><path d="M5 9h7M9 6l3 3-3 3" fill="none" stroke="#c0151b" stroke-width="1.6"/></svg></a>
<div class="abs post-photo" style="left:774px;top:1398px;width:310px;height:218px;background:radial-gradient(circle at 50% 45%,#ffffff,#e2e2e2 60%,#cfcfcf)" role="img" aria-label="Illustration d'un cube blanc avec une croix rouge sur le dessus"></div>

<svg class="abs twitter-feed" viewBox="0 0 1200 284" role="presentation">
  <path d="M0 0H560Q592 0 597 30Q602 0 634 0H1200V284H838Q818 284 813 266Q808 284 788 284H336Q316 284 311 266Q306 284 286 284H164Q144 284 139 266Q134 284 114 284H0Z" fill="#56595c"/>
  <path d="M0 0H560Q592 0 602 -20Q612 0 644 0" fill="none"/>
  <path d="M366 87H548M658 87H840" stroke="#7a7d80" stroke-width="1.5"/>
  <circle cx="602" cy="87" r="13" fill="#ffffff"/>
</svg>
<p class="abs tweet">Velit esse cillum dolore eu fugiat nulla pariatur. Excepteur sint oc-<br>caecat cupidatat non proident. <b>@SoleneBrivard #EnjeuSanté</b></p>
<p class="abs follow">Follow <b>@Velmora_Rcrt</b></p>

<footer>
  <div class="abs" style="left:132px;top:2010px">
    <h4 class="footer-head">Links</h4>
    <ul class="footer-links">
      <li><a href="#">Accueil</a></li><li><a href="#">Agence</a></li><li><a href="#">Services</a></li>
      <li><a href="#">Approche</a></li><li><a href="#">Publications</a></li><li><a href="#">Contact</a></li>
    </ul>
  </div>
  <div class="abs" style="left:284px;top:2010px">
    <h4 class="footer-head">Connect</h4>
    <div class="connect-icons"><span></span><span></span><span></span></div>
    <p class="copyright">(c) Solène Brivard. Tous droits réservés.</p>
  </div>
  <div class="abs" style="left:752px;top:2010px">
    <h4 class="footer-head">Recevez nos publications</h4>
    <div class="field" style="margin-top:15px">Votre nom</div>
    <div class="field">Votre courriel</div>
    <div class="subscribe">Abonnez-vous</div>
  </div>
</footer>

</body>
</html>
```